In need of an AWESOME website for our Water Re-filling Store

The project is to design a website for our retail store front with the website www.quellbrookfillhouse.com. Currently if you go to that site it redirects you to our other site www.quellbrookbottleworks.com which is just our water bottle website. So, I need a new website created for www.quellbrookfillhouse.com (retail storefront)
Use our Squarespace to create a site with pages to help educate, tell about us, link to our water bottle brand site that is already created with Squarespace, and show the family and community aspects that we believe in. Our current water bottle website is www.quellbrookbottleworks.com for reference
We also sell hydration products, especially PRZQ products and have access to digital media through our PRZQ dealer site. we sell bottles, dispensers and other supplies for water refilling customers. We sell Ice as well.

Target Market(s)

Local residents looking to fill up their 1-5 gallon water jugs

Industry/Entity Type

Alkaline and Purified Water Retail Re-filling Store

Coding

Coded - Design and coding required

Font styles to use
Serif
Sans Serif

Colors
0054AA
0677BA
7BADD7
CADEEF
E8F1F8

Requirements
Must have
• pictures of our family in the about us section and pictures of our store inside and out.

```html
<!DOCTYPE html>
<html lang="en">
<head>
<meta charset="utf-8">
<title>Quellbrook Fill House</title>
<link href="https://fonts.googleapis.com/css2?family=Poppins:ital,wght@0,400;0,500;0,600;0,700;1,400&display=swap" rel="stylesheet">
<style>
:root{
  --navy:#0054AA;
  --blue:#0677BA;
  --sky:#7BADD7;
  --mist:#CADEEF;
  --ice:#E3EDF7;
  --ink:#1c1c1c;
  --body:#3a3a3a;
  --footer:#1f2023;
  --star:#f59a12;
}
*{box-sizing:border-box;margin:0;padding:0}
html,body{width:1200px;height:4170px;overflow:hidden}
body{font-family:'Poppins',sans-serif;color:var(--ink);background:#fff;position:relative}
.abs{position:absolute}
section{position:absolute;left:0;width:1200px}
p{font-size:14.5px;line-height:24px;color:var(--body)}
.title{font-size:41px;font-weight:400;line-height:46px;color:var(--ink)}
.title b{color:var(--navy);font-weight:600}
.title em{font-style:normal;color:var(--blue)}
.btn{position:absolute;display:flex;align-items:center;gap:14px;height:50px;padding:0 14px 0 38px;background:var(--navy);color:#fff;font-size:15.5px;text-decoration:none;border-bottom:3px solid #003f82}
.drop{width:30px;height:30px;border-radius:50%;background:#fff;display:flex;align-items:center;justify-content:center}
.brand-disc{position:absolute;border-radius:50%;background:#fff;display:flex;align-items:center;justify-content:center;text-align:center;color:var(--navy);font-weight:600;line-height:1.15}

/* hero */
.hero{top:0;height:720px;background:linear-gradient(100deg,#3f4448 0%,#5a6063 45%,#2e3a5a 75%,#1e3a8a 100%);overflow:hidden}
.nav{position:absolute;top:76px;right:74px;display:flex;gap:42px;font-size:15.5px;color:#e8e8e8}
.nav a{color:inherit;text-decoration:none}
.nav .active{color:var(--sky);font-weight:600;border-bottom:2px solid var(--sky);padding-bottom:2px}
.hero h1{position:absolute;left:75px;top:242px;font-size:46px;line-height:58px;color:#fff;font-weight:700}
.hero h1 span{display:block;font-weight:500}
.hero .lede{position:absolute;left:75px;top:362px;width:560px;font-size:22.5px;line-height:29px;color:#fff}
.hero-products{position:absolute;left:625px;top:320px;width:560px;height:400px;border-radius:30px 30px 0 0;background:radial-gradient(ellipse at 50% 40%,#bcd9f2 0%,#6aa6dc 45%,#2f66b8 100%)}

/* welcome */
.welcome{top:720px;height:640px}
.ring-back{position:absolute;border-radius:50%;background:var(--navy)}
.photo-circle{position:absolute;border-radius:50%;border:9px solid #fff}

/* products */
.products{top:1290px;height:590px;background:var(--ice)}
.card{position:absolute;top:215px;width:242px;text-align:center}
.card .shot{height:222px;background:#fff;display:flex;align-items:center;justify-content:center}
.card h3{margin-top:18px;font-size:16px;font-weight:600;color:var(--blue)}
.card p{font-size:14.5px;line-height:21px;margin-top:2px}
.arrow{position:absolute;top:350px}

/* store */
.store{top:1880px;height:550px}
.img-box{position:absolute}

/* testimonial */
.testimonials{top:2430px;height:460px;background:var(--ice)}
.quote-card{position:absolute;left:226px;top:65px;width:748px;height:330px;background:#fff;text-align:center}
.stars{margin-top:60px;display:flex;justify-content:center;gap:6px}
.quote-card blockquote{margin:14px auto 0;width:690px;font-style:italic;font-size:16.5px;line-height:30px;color:#333}
.quote-card h4{margin-top:12px;color:var(--navy);font-size:16px;font-weight:600}
.dots{margin-top:38px;display:flex;justify-content:center;gap:10px}
.dots i{width:42px;height:3px;background:#555}
.dots i.on{background:var(--navy)}

/* supplies */
.supplies{top:2890px;height:585px}

/* newsletter */
.newsletter{top:3475px;height:300px;background:var(--ice);text-align:center}
.newsletter h2{margin-top:58px;font-size:43px;font-weight:400}
.newsletter h2 b{color:var(--navy);font-weight:600}
.newsletter p{margin-top:6px;font-size:14.5px}
.signup{position:absolute;left:317px;top:153px;width:563px;height:52px;background:#fff;display:flex;align-items:center;justify-content:space-between;padding:0 6px 0 18px}
.signup span{font-size:14.5px;color:#333}
.signup button{font-family:inherit;background:var(--navy);color:#fff;border:0;font-weight:600;font-size:15px;height:38px;width:100px}

/* footer */
.footer{top:3720px;height:450px;background:var(--footer);color:#d8d8d8}
.footer h5{font-size:19px;font-weight:600;color:#fff;margin-bottom:14px}
.footer h5 span{font-weight:400}
.col{position:absolute;top:170px;font-size:14.5px;line-height:33.5px}
.col a{color:#d8d8d8;text-decoration:none;display:block}
.col .link{color:var(--sky);text-decoration:underline}
.copy{position:absolute;left:70px;top:357px;width:250px;text-align:center;font-size:12.5px;line-height:20px;color:#ddd}
.social{display:flex;gap:24px;margin-top:4px}
.social i{display:block;width:28px;height:28px;border:2.5px solid var(--blue);border-radius:6px}
.social i.fill{background:#fff;border-color:#fff}
</style>
</head>
<body>

<section class="hero">
  <div class="abs" style="inset:0" role="img" aria-label="Photo of the store interior with refill stations"></div>
  <div class="brand-disc" style="left:76px;top:22px;width:140px;height:140px;font-size:16px;box-shadow:0 0 0 7px var(--navy)">Quellbrook<br>Fill House</div>
  <nav class="nav">
    <a class="active" href="#">Home</a><a href="#">About Us</a><a href="#">Products</a><a href="#">Blog</a><a href="#">Testimonials</a><a href="#">Contact Us</a>
  </nav>
  <h1>Elevate Your Hydration.<span>Empower the Planet.</span></h1>
  <p class="lede">Premium alkaline water in refillable aluminum bottles — made for active, eco-conscious lifestyles.</p>
  <a class="btn" href="#" style="left:76px;top:470px">Read More <span class="drop"><svg width="14" height="18" viewBox="0 0 14 18"><path d="M7 1C4 6 1 9 1 12a6 6 0 0 0 12 0c0-3-3-6-6-11z" fill="none" stroke="#0054AA" stroke-width="2"/></svg></span></a>
  <div class="hero-products" role="img" aria-label="Five-gallon water jugs with canned and bottled hydration drinks"></div>
  <svg class="abs" style="left:0;top:610px" width="1200" height="110" viewBox="0 0 1200 110">
    <path d="M0 110 L0 100 C220 40 420 40 640 70 C860 100 1020 60 1200 40 L1200 110Z" fill="#fff"/>
    <path d="M40 100 C240 40 460 40 640 66 C500 50 300 55 40 100Z" fill="var(--navy)"/>
    <path d="M560 90 C760 100 980 70 1200 32 L1200 48 C1000 80 800 105 560 90Z" fill="var(--navy)"/>
  </svg>
</section>

<section class="welcome">
  <div class="ring-back" style="left:75px;top:75px;width:450px;height:450px"></div>
  <div class="photo-circle" style="left:80px;top:62px;width:440px;height:440px;background:linear-gradient(170deg,#d8d2c6 0%,#b9b2a4 50%,#8e8b83 100%)" role="img" aria-label="Family photo of the owners standing together on the beach"></div>
  <h2 class="title abs" style="left:586px;top:80px">Welcome to <b>Quellbrook</b><br><em>Fill House</em></h2>
  <div class="abs" style="left:586px;top:190px;width:520px">
    <p>Nemo enim ipsam voluptatem quia voluptas sit aspernatur aut odit aut fugit, sed quia consequuntur magni dolores eos qui ratione voluptatem sequi nesciunt. Neque porro quisquam est, qui dolorem ipsum quia dolor sit amet, consectetur, adipisci velit, sed quia non numquam eius modi tempora incidunt ut labore et dolore magnam aliquam quaerat voluptatem.</p>
    <p style="margin-top:14px">Nemo enim ipsam voluptatem quia voluptas sit aspernatur aut odit aut fugit, sed quia consequuntur magni dolores eos qui ratione voluptatem sequi nesciunt.</p>
  </div>
  <a class="btn" href="#" style="left:586px;top:445px">Read More <span class="drop"><svg width="14" height="18" viewBox="0 0 14 18"><path d="M7 1C4 6 1 9 1 12a6 6 0 0 0 12 0c0-3-3-6-6-11z" fill="none" stroke="#0054AA" stroke-width="2"/></svg></span></a>
</section>

<section class="products">
  <svg class="abs" style="left:0;top:0" width="1200" height="80" viewBox="0 0 1200 80">
    <path d="M0 0 L1200 0 L1200 20 C1000 10 850 40 700 60 C500 40 250 10 0 10Z" fill="#fff"/>
    <path d="M40 12 C220 20 420 40 690 60 C430 30 250 10 40 12Z" fill="var(--navy)"/>
    <path d="M560 62 C760 60 900 5 1200 15 L1200 30 C950 18 800 60 560 62Z" fill="var(--navy)"/>
  </svg>
  <h2 class="title abs" style="left:0;width:1200px;text-align:center;top:135px">Our <b>Quellbrook</b> <em>Hydration Products</em></h2>
  <svg class="arrow" style="left:42px" width="20" height="32" viewBox="0 0 20 32"><path d="M16 2 L4 16 L16 30" fill="none" stroke="var(--navy)" stroke-width="2.5"/></svg>
  <svg class="arrow" style="left:1138px" width="20" height="32" viewBox="0 0 20 32"><path d="M4 2 L16 16 L4 30" fill="none" stroke="var(--navy)" stroke-width="2.5"/></svg>
  <div class="card" style="left:75px"><div class="shot"><div style="width:70px;height:185px;border-radius:10px;background:linear-gradient(90deg,#1b1b1b,#3a3a3a 60%,#9ccf3a)" role="img" aria-label="PRZQ sparkling drink can"></div></div><h3>PRZQ Products</h3><p>Nemo enim ipsam voluptatem<br>quia voluptas</p></div>
  <div class="card" style="left:345px"><div class="shot"><div style="width:52px;height:185px;border-radius:14px 14px 8px 8px;background:linear-gradient(90deg,#2d3a22,#4e5e36)" role="img" aria-label="Bottled green juice drink"></div></div><h3>Flavoured Drinks</h3><p>Nemo enim ipsam voluptatem<br>quia voluptas</p></div>
  <div class="card" style="left:614px"><div class="shot"><div style="width:80px;height:175px;border-radius:10px;background:linear-gradient(90deg,#9a9a9a,#e2e2e2 45%,#d8cf4a 70%,#8e8e8e)" role="img" aria-label="Can of hops flavoured kombucha"></div></div><h3>Flavoured Kombucha</h3><p>Nemo enim ipsam voluptatem<br>quia voluptas</p></div>
  <div class="card" style="left:884px"><div class="shot"><div style="width:190px;height:130px;border-radius:20px;background:linear-gradient(160deg,#f3f6f9,#cdd6df)" role="img" aria-label="Bag of packaged ice"></div></div><h3>Ice Packs</h3><p>Nemo enim ipsam voluptatem<br>quia voluptas</p></div>
</section>

<section class="store">
  <h2 class="title abs" style="left:75px;top:100px;line-height:41px">About <b>Quellbrook</b> <em>Fill</em><br><em>House Store</em></h2>
  <p class="abs" style="left:75px;top:198px;width:420px">Nemo enim ipsam voluptatem quia voluptas sit aspernatur aut odit aut fugit, sed quia consequuntur magni dolores eos qui ratione voluptatem sequi nesciunt. Neque porro quisquam est, qui dolorem ipsum quia dolor sit amet, consectetur, adipisci velit, sed quia non numquam eius modi tempora incidunt ut labore et dolore magnam aliquam quaerat .</p>
  <a class="btn" href="#" style="left:75px;top:395px;padding-left:24px">Visit Our Store <span class="drop"><svg width="14" height="18" viewBox="0 0 14 18"><path d="M7 1C4 6 1 9 1 12a6 6 0 0 0 12 0c0-3-3-6-6-11z" fill="none" stroke="#0054AA" stroke-width="2"/></svg></span></a>
  <div class="img-box" style="left:704px;top:70px;width:422px;height:382px;background:linear-gradient(180deg,#b59b6e 0%,#c9ae7e 45%,#8a7b62 100%)" role="img" aria-label="Storefront exterior with the shop banner over the door"></div>
  <div class="img-box" style="left:528px;top:238px;width:322px;height:240px;border:4px solid #fff;background:linear-gradient(110deg,#3d4a62 0%,#6d86b0 40%,#e4e6ea 60%,#c8ccd2 100%)" role="img" aria-label="Water filtration equipment and storage tanks inside the store"></div>
</section>

<section class="testimonials">
  <div class="quote-card">
    <div class="stars">
      <svg width="110" height="18" viewBox="0 0 110 18"><g fill="var(--star)"><path id="st" d="M9 0l2.6 5.6 6.1.7-4.5 4.2 1.2 6L9 13.5 3.6 16.5l1.2-6L.3 6.3l6.1-.7z"/><use href="#st" x="23"/><use href="#st" x="46"/><use href="#st" x="69"/><use href="#st" x="92"/></g></svg>
    </div>
    <blockquote>“ Nemo enim ipsam voluptatem quia voluptas sit &nbsp;aspernatur aut odit aut fugit, sed quia consequuntur magni dolores eos qui ratione voluptatem sequi nesciunt. Neque porro quisquam est..”</blockquote>
    <h4>Name Heading</h4>
    <div class="dots"><i></i><i class="on"></i><i></i><i></i></div>
  </div>
</section>

<section class="supplies">
  <div class="ring-back" style="left:75px;top:65px;width:450px;height:450px"></div>
  <div class="photo-circle" style="left:80px;top:52px;width:440px;height:440px;background:linear-gradient(180deg,#eef0f3 0%,#2a2d33 40%,#3a3d44 70%,#e9ebee 100%)" role="img" aria-label="Store wall display of water bottles, tumblers and dispensers"></div>
  <h2 class="title abs" style="left:586px;top:112px;font-size:43px;line-height:47px">We sell <b>Bottles,Dispensers</b><br>and other supplies for<br><em>water refilling</em></h2>
  <p class="abs" style="left:586px;top:268px;width:520px">Nemo enim ipsam voluptatem quia voluptas sit aspernatur aut odit aut fugit, sed quia consequuntur magni dolores eos qui ratione voluptatem sequi nesciunt. Neque porro quisquam est, qui dolorem ipsum quia dolor sit amet, consectetur, adipisci velit, sed quia non numquam eius modi tempora incidunt ut labore et dolore magnam aliquam quaerat voluptatem.</p>
  <a class="btn" href="#" style="left:586px;top:420px">Read More <span class="drop"><svg width="14" height="18" viewBox="0 0 14 18"><path d="M7 1C4 6 1 9 1 12a6 6 0 0 0 12 0c0-3-3-6-6-11z" fill="none" stroke="#0054AA" stroke-width="2"/></svg></span></a>
</section>

<section class="newsletter">
  <h2>Newsletter <b>Subscribe</b></h2>
  <p>Nemo enim ipsam voluptatem quia voluptas sit aspernatur aut odit aut fugit, sed quia consequuntur magni</p>
  <div class="signup"><span>Email Address</span><button>Sign Up</button></div>
</section>

<section class="footer">
  <svg class="abs" style="left:0;top:0" width="1200" height="110" viewBox="0 0 1200 110">
    <rect width="1200" height="110" fill="var(--footer)"/>
    <path d="M0 0 L1200 0 L1200 20 C1000 10 850 40 700 70 C500 40 250 10 0 10Z" fill="var(--ice)"/>
    <path d="M40 12 C220 20 420 40 700 70 C430 30 250 10 40 12Z" fill="var(--navy)"/>
    <path d="M560 72 C760 70 900 5 1200 15 L1200 32 C950 22 800 70 560 72Z" fill="var(--navy)"/>
  </svg>
  <div class="brand-disc" style="left:110px;top:172px;width:170px;height:170px;font-size:18px;box-shadow:0 0 0 8px var(--navy)">Quellbrook<br>Fill House</div>
  <div class="copy">Copyright © 2026 Company Name<br>All Rights Reserved</div>
  <div class="col" style="left:364px">
    <h5>Quick <span>Links</span></h5>
    <a href="#">Home</a><a href="#">About Us</a><a href="#">Products</a><a href="#">Blog</a><a href="#">Testimonials</a><a href="#">Contact Us</a>
  </div>
  <div class="col" style="left:590px">
    <h5>Contact <span>Us</span></h5>
    <div style="line-height:26px">2475 W. Larkmeadow Rd., Ste. 40<br>Fairhollow, AZ 85099</div>
    <div style="margin-top:4px">(555) 014-2286</div>
    <div>info@quellbrookfillhouse.com</div>
    <a class="link" href="#">Map Direction</a>
  </div>
  <div class="col" style="left:884px">
    <h5>Business <span>Hours</span></h5>
    <div style="line-height:29px">Tuesday–Friday 9am–6pm<br>Saturday &amp; Sunday 10am–5pm<br>Closed on Mondays</div>
    <h5 style="margin-top:18px;margin-bottom:8px">Follow Us</h5>
    <div class="social"><i aria-label="Social profile link"></i><i class="fill" aria-label="Social profile link"></i></div>
  </div>
</section>

</body>
</html>
```